Business card for medical clinic

I need an upmarket, modern medical/health business card for my clinic

Contact Information for Business Card

name, address, email, qr code

```html
<!DOCTYPE html>
<html lang="en">
<head>
<meta charset="utf-8">
<title>Meridia Health Group – Business Card</title>
<link href="https://fonts.googleapis.com/css2?family=Montserrat:wght@400;500;600&display=swap" rel="stylesheet">
<style>
  :root{
    --page:#d9d4ce;
    --card-light:#e8dfd3;
    --card-light-2:#d6cabb;
    --card-dark:#2c2a28;
    --card-dark-2:#1f1e1d;
    --teal:#2a93a9;
    --teal-soft:#6fb6c6;
    --navy:#1c4a68;
    --ink-soft:#cbbfb0;
    --icon:#3c8192;
  }
  *{margin:0;padding:0;box-sizing:border-box}
  html,body{width:1200px;height:1047px;overflow:hidden}
  body{background:var(--page);font-family:"Montserrat",sans-serif;position:relative}
  .business-card{
    position:absolute;left:80px;top:240px;width:1040px;height:568px;
    border-radius:26px;overflow:hidden;
    background:linear-gradient(160deg,var(--card-light),var(--card-light-2));
    box-shadow:0 10px 30px rgba(0,0,0,.15);
  }
  .accent-band{
    position:absolute;left:0;right:0;top:214px;height:22px;
    background:linear-gradient(90deg,var(--navy),var(--teal) 55%,var(--teal-soft));
    opacity:.85;
  }
  .dark-panel{
    position:absolute;left:0;right:0;top:244px;bottom:0;
    background:linear-gradient(160deg,var(--card-dark),var(--card-dark-2));
  }
  .brand{position:absolute;right:38px;top:88px;display:flex;align-items:center;gap:18px}
  .brand-dot{width:30px;height:30px;border-radius:50%;background:var(--navy)}
  .brand-name{color:var(--navy);font-weight:500;font-size:36px;line-height:1.1;letter-spacing:1px}
  .brand-name span{display:block;font-size:21px;letter-spacing:6px;text-align:center}
  .holder{position:absolute;left:41px;top:278px}
  .holder-name{color:var(--teal);font-weight:600;font-size:44px;letter-spacing:1px;line-height:1}
  .holder-role{color:var(--ink-soft);font-weight:400;font-size:26px;margin-top:12px;line-height:1}
  .contacts{position:absolute;left:41px;top:426px;list-style:none}
  .contacts li{display:flex;align-items:center;gap:10px;color:var(--ink-soft);font-size:26px;line-height:1;height:39px}
  .contacts svg{width:22px;height:22px;flex:none}
  .address{position:absolute;right:35px;top:466px;text-align:right;color:var(--ink-soft);font-size:26px;line-height:39px}
</style>
</head>
<body>
  <div class="business-card">
    <div class="accent-band" role="img" aria-label="Decorative teal wave accent"></div>
    <div class="dark-panel"></div>

    <div class="brand">
      <div class="brand-dot"></div>
      <div class="brand-name">MERIDIA HEALTH<span>GROUP</span></div>
    </div>

    <div class="holder">
      <div class="holder-name">DANIEL HART</div>
      <div class="holder-role">Managing Director</div>
    </div>

    <ul class="contacts">
      <li><svg viewBox="0 0 24 24"><path fill="var(--icon)" d="M6.6 10.8a15 15 0 0 0 6.6 6.6l2.2-2.2c.3-.3.7-.4 1-.2 1.1.4 2.3.6 3.6.6.6 0 1 .4 1 1V20c0 .6-.4 1-1 1A17 17 0 0 1 3 4c0-.6.4-1 1-1h3.5c.6 0 1 .4 1 1 0 1.3.2 2.5.6 3.6.1.3 0 .7-.2 1z"/></svg>123 456 789</li>
      <li><svg viewBox="0 0 24 24"><rect x="3" y="6" width="18" height="13" rx="1.5" fill="var(--icon)"/><path d="M3.5 7l8.5 6.5L20.5 7" fill="none" stroke="#2a2826" stroke-width="1.5"/></svg>hello@clinicmail.com</li>
      <li><svg viewBox="0 0 24 24"><circle cx="12" cy="12" r="9" fill="var(--icon)"/><path d="M3 12h18M12 3c3 3 3 15 0 18M12 3c-3 3-3 15 0 18" fill="none" stroke="#2a2826" stroke-width="1.2"/></svg>www.yourwebsite.com</li>
    </ul>

    <div class="address">Your address, City<br>State, Zip 1234</div>
  </div>
</body>
</html>
```